Request for Business Card Design

Hi. My name is Marlene, I am looking for a new business card design for my company, Quarrow Signal Instruments, LLC. I really like the design you did for Tarsel Venture and was hoping you could do something similar using our full logo and our mark. I am also open to any raised texture design using our mark. I have attached our full logo, which would need to be somewhere on the card, as well as the mark in both outline and full form, as well as our brand colors / guide. The card does not have to be white, as long as our logo and mark appear. I actually like darker colored business cards more, but am open to all options. If you are interested in working with me, please let me know. We would also take the business card design into letterhead design if you can do that.

```html
<!DOCTYPE html>
<html lang="en">
<head>
<meta charset="utf-8">
<title>Quarrow Signal Instruments – Business Card</title>
<link rel="stylesheet" href="https://fonts.googleapis.com/css2?family=Open+Sans:wght@400;700;800&display=swap">
<style>
  :root {
    --brand-blue: #1399c2;
    --brand-blue-soft: #3aa9cd;
    --ink: #333333;
    --paper: #ffffff;
    --backdrop: #2a2a2a;
  }
  * { box-sizing: border-box; margin: 0; padding: 0; }
  html, body { width: 1200px; height: 900px; overflow: hidden; }
  body {
    background: var(--backdrop);
    font-family: "Open Sans", sans-serif;
    position: relative;
  }
  .card {
    position: absolute;
    width: 560px;
    height: 320px;
    overflow: hidden;
    box-shadow: 0 12px 30px rgba(0,0,0,0.45);
  }
  .card--front { left: 320px; top: 90px; background: var(--paper); border-bottom: 5px solid var(--brand-blue); }
  .card--back  { left: 320px; top: 490px; background: var(--brand-blue); }

  /* Wordmark */
  .wordmark { position: absolute; display: flex; align-items: center; gap: 12px; }
  .wordmark__dot { border-radius: 50%; flex: none; }
  .wordmark__name { font-weight: 800; line-height: 1; letter-spacing: 0.06em; text-transform: uppercase; }
  .wordmark__name span { display: block; }
  .wordmark__line2 { font-size: 0.42em; letter-spacing: 0.08em; margin-top: 5px; }

  .card--front .wordmark { left: 52px; top: 30px; color: var(--ink); }
  .card--front .wordmark__dot { width: 38px; height: 38px; background: var(--brand-blue); }
  .card--front .wordmark__name { font-size: 30px; }

  .card--back .wordmark { left: 60px; top: 110px; color: var(--paper); }
  .card--back .wordmark__dot { width: 70px; height: 70px; background: var(--paper); }
  .card--back .wordmark__name { font-size: 52px; }

  /* Front details */
  .accent-bar { position: absolute; left: 28px; top: 100px; width: 12px; height: 34px; background: var(--brand-blue); }
  .holder { position: absolute; left: 52px; top: 100px; }
  .holder__name { color: var(--brand-blue); font-weight: 700; font-size: 22px; text-transform: uppercase; letter-spacing: 0.02em; line-height: 1.1; }
  .holder__title { color: var(--ink); font-size: 14px; margin-top: 2px; }
  .address { position: absolute; left: 52px; top: 168px; color: var(--ink); font-size: 14px; line-height: 1.45; }
  .contacts { position: absolute; left: 38px; top: 222px; list-style: none; color: var(--ink); font-size: 14px; line-height: 1.6; }
  .contacts li { display: flex; align-items: center; gap: 7px; }
  .contacts svg { width: 11px; height: 11px; fill: var(--brand-blue); flex: none; }

  .front-decor { position: absolute; right: -40px; bottom: -80px; width: 280px; height: 280px; border-radius: 50%; border: 46px solid var(--brand-blue); }
  .back-decor { position: absolute; right: -60px; top: -40px; width: 380px; height: 380px; border-radius: 50%; border: 60px solid var(--brand-blue-soft); opacity: 0.6; }
</style>
</head>
<body>

<section class="card card--front" aria-label="Business card front">
  <div class="front-decor"></div>
  <div class="wordmark">
    <div class="wordmark__dot"></div>
    <div class="wordmark__name"><span>Quarrow</span><span class="wordmark__line2">Signal Instruments</span></div>
  </div>
  <div class="accent-bar"></div>
  <div class="holder">
    <div class="holder__name">Owen Castell</div>
    <div class="holder__title">Managing Director</div>
  </div>
  <div class="address">Your address, City<br>State, Zip 1234</div>
  <ul class="contacts">
    <li><svg viewBox="0 0 24 24"><path d="M6.6 10.8a15 15 0 0 0 6.6 6.6l2.2-2.2c.3-.3.7-.4 1-.2 1.1.4 2.3.6 3.6.6.6 0 1 .4 1 1V20c0 .6-.4 1-1 1A17 17 0 0 1 3 4c0-.6.4-1 1-1h3.5c.6 0 1 .4 1 1 0 1.3.2 2.5.6 3.6.1.3 0 .7-.2 1z"/></svg>123 456 789</li>
    <li><svg viewBox="0 0 24 24"><path d="M2 5h20v14H2z M2 5l10 8 10-8" /></svg>info@quarrowsignal.com</li>
    <li><svg viewBox="0 0 24 24"><circle cx="12" cy="12" r="10"/></svg>www.quarrowsignal.com</li>
  </ul>
</section>

<section class="card card--back" aria-label="Business card back">
  <div class="back-decor"></div>
  <div class="wordmark">
    <div class="wordmark__dot"></div>
    <div class="wordmark__name"><span>Quarrow</span><span class="wordmark__line2">Signal Instruments</span></div>
  </div>
</section>

</body>
</html>
```